Business Card Design Project

I need a business card designed that is clean, simple and elegant.
I am a fashion and advertising photographer based in Cape Town and Durban South Africa.
check out my website: www.marekvollan.co.za for ideas
Updates
Hi all,
Thanks for your submissions so far!
Please note:
I want no more than than black, white and/or grey to be used.
I don't want any photos used.
I would like the card to be double sided.
I would like to continue the design similar to the past ones Ive used.
I hope this helps, please send me further questions should you have any.
many thanks!
Marek
Hi,
Please have a look at the jpg I loaded(called inspiration) which is the direction or inspiration I am aiming at.
Also PLEASE remember NO PHOTOS to be included on the card
many thanks!!
Target Market(s)
You can look at my site to get a better understanding of the audience:
www.marekvollan.co.za
Industry/Entity Type
Advertising
Requirements
Must have
- Clean design which can also be used for a watermark on photographs
perhaps black background with white text/grey
company called: Marek Vollan Photography
Nice to have
- below I have added logos that I have used in the past.
Should not have
- pictures of cameras
tacky elements

```html
<!DOCTYPE html>
<html lang="en">
<head>
<meta charset="UTF-8">
<title>Marek Vollan Photography – Business Card</title>
<link rel="stylesheet" href="https://fonts.googleapis.com/css2?family=Bodoni+Moda:wght@400;500&family=Saira:wght@500&display=swap">
<style>
  :root {
    --card-ground: #c4c4c4;
    --block-grey: #959595;
    --overlap-grey: #727272;
    --name-white: #ffffff;
    --tagline-black: #000000;
  }
  html, body {
    margin: 0;
    padding: 0;
    overflow: hidden;
    background: var(--card-ground);
  }
  .card {
    position: relative;
    width: 1200px;
    height: 667px;
    background: var(--card-ground);
    overflow: hidden;
  }
  .card__shapes {
    position: absolute;
    inset: 0;
  }
  .shape--block { fill: var(--block-grey); }
  .shape--overlap { fill: var(--overlap-grey); }
  .identity {
    position: absolute;
    left: 105px;
    width: 643px;
    top: 245px;
    text-align: center;
  }
  .identity__name {
    margin: 0;
    font-family: "Bodoni Moda", "Didot", serif;
    font-weight: 400;
    font-size: 84px;
    line-height: 84px;
    letter-spacing: 6px;
    color: var(--name-white);
    text-transform: uppercase;
  }
  .identity__name span { display: block; }
  .identity__tagline {
    margin: 24px 0 0;
    font-family: "Saira", sans-serif;
    font-weight: 500;
    font-size: 34px;
    line-height: 40px;
    letter-spacing: 0.5px;
    color: var(--tagline-black);
  }
</style>
</head>
<body>
  <div class="card">
    <svg class="card__shapes" width="1200" height="667" viewBox="0 0 1200 667" aria-hidden="true">
      <rect class="shape--block" x="105" y="0" width="643" height="619"/>
      <rect class="shape--block" x="748" y="498" width="452" height="121"/>
      <rect class="shape--block" x="700" y="619" width="48" height="48"/>
      <rect class="shape--overlap" x="700" y="498" width="48" height="121"/>
    </svg>
    <div class="identity">
      <h1 class="identity__name"><span>Marek</span><span>Vollan</span></h1>
      <p class="identity__tagline">........Photography........</p>
    </div>
  </div>
</body>
</html>
```